Brelvo Orthodontics Exterior Signage

We need 4 exterior signs designed for our orthodontics practice based in Sydney, Australia. The signs face busy streets and walkways and experience heavy foot traffic. The existing signage has been in use for about 5 years and is starting to feel outdated. We want the signs to be clean and modern with effective use of brand colours and imagery. For details about the practice and brand style, see: brelvoorthodontics.com.au

Target Market(s)

Foot traffic in affluent suburb of Sydney, Australia.

Industry/Entity Type

Health Care

Font styles to use
Sans Serif

Colors

Designer to choose colors to be used in the design.

Requirements
Must have
• Modern, clean, professional feel. Family friendly.
Nice to have
• Effective use of lifestyle imagery. For similar examples, see: https://www.tandrevo.com.au
Should not have
• No close-up imagery of teeth or mouths.

```html
<!DOCTYPE html>
<html lang="en">
<head>
<meta charset="utf-8">
<title>Brelvo Orthodontics – Entrance Banner</title>
<link href="https://fonts.googleapis.com/css2?family=Varela+Round&family=Mulish:wght@400;600;700&display=swap" rel="stylesheet">
<style>
  :root {
    --bg: #e9ebec;
    --panel: #f3f4f4;
    --green: #2e8a72;
    --purple: #6a2c7e;
    --white: #ffffff;
    --photo-top: #d9ccbe;
    --photo-bottom: #8a6f78;
  }
  html, body {
    margin: 0;
    padding: 0;
    width: 1200px;
    height: 923px;
    overflow: hidden;
    background: var(--bg);
  }
  .canvas {
    position: relative;
    width: 1200px;
    height: 923px;
  }
  .banner {
    position: absolute;
    left: 436px;
    top: 31px;
    width: 328px;
    height: 860px;
    box-shadow: 0 2px 10px rgba(0,0,0,0.12);
  }
  .banner svg { display: block; width: 100%; height: 100%; }
  .brand-name {
    font-family: "Mulish", sans-serif;
    font-weight: 600;
    font-size: 19px;
    fill: var(--purple);
  }
  .headline {
    font-family: "Varela Round", sans-serif;
    font-size: 42px;
    fill: var(--green);
  }
  .entrance-label {
    font-family: "Mulish", sans-serif;
    font-weight: 600;
    font-size: 56px;
    fill: var(--purple);
    letter-spacing: 1px;
  }
</style>
</head>
<body>
<main class="canvas">
  <div class="banner">
    <svg viewBox="0 0 347 910" preserveAspectRatio="none" xmlns="http://www.w3.org/2000/svg">
      <defs>
        <linearGradient id="family-photo-tone" x1="0" y1="0" x2="0" y2="1">
          <stop offset="0" stop-color="var(--photo-top)"/>
          <stop offset="1" stop-color="var(--photo-bottom)"/>
        </linearGradient>
      </defs>

      <rect class="panel-bg" x="0" y="0" width="347" height="910" fill="var(--panel)"/>

      <g class="brand">
        <circle class="brand-dot" cx="98" cy="52" r="9" fill="var(--green)"/>
        <text class="brand-name" x="114" y="59">brelvo orthodontics</text>
      </g>

      <g class="headline">
        <text x="340" y="116" text-anchor="end">Creating</text>
        <text x="340" y="162" text-anchor="end">great, straight</text>
        <text x="340" y="208" text-anchor="end">smiles</text>
      </g>

      <path class="family-photo" role="img" aria-label="Lifestyle photo of a smiling family of four: father, mother, daughter and son"
            d="M0,224 H347 V400 Q180,440 0,478 Z" fill="url(#family-photo-tone)"/>

      <path class="swoosh-green" d="M0,478 Q180,440 347,400 L347,452 Q260,472 185,500 L0,500 Z" fill="var(--green)"/>
      <path class="swoosh-purple" d="M185,500 Q260,472 347,452 L347,500 Z" fill="var(--purple)"/>

      <rect class="entrance-band" x="0" y="500" width="347" height="137" fill="var(--white)"/>
      <text class="entrance-label" x="173.5" y="552" text-anchor="middle">ENTRANCE</text>

      <g class="entrance-arrows" fill="var(--purple)">
        <polygon points="100,565 130,565 160,595 130,625 100,625 130,595"/>
        <polygon points="145,565 175,565 205,595 175,625 145,625 175,595"/>
        <polygon points="190,565 220,565 250,595 220,625 190,625 220,595"/>
      </g>

      <rect class="base-block" x="0" y="637" width="347" height="273" fill="var(--purple)"/>
    </svg>
  </div>
</main>
</body>
</html>
```